Website Redesign for Non-Profit Ministry & Church

NOTE: Please do not contact me privately — all private inquiries will be ignored.

Individuals seeking spiritual healing, community connection, ministry support and journal-based encounters.

Description of What’s Needed

We need a clean, fresh, inviting website that encourages engagement and connection. The site should feel warm and accessible, draw people in, and clearly present who we are, what we offer, and how visitors can participate. The layout should be straightforward, with well-structured pages (no overlapping objects, minimal layering complexity) and easy to navigate. Use only Google Fonts. All stock photos must be sourced from royalty-free sites and include proper attribution. We will not include a search feature.

Pages to Create
1. Home Page – impactful hero area, clear call-to-action, visual story of ministry, giving/gathering invitation.
2. About Us – vision, mission, leadership, testimonies, history.
3. Meetings & Events – upcoming gatherings, schedule, how to attend, sign-up or interest form.
4. Encounter: “Lanterns by the River” (book) – dedicated page for the book, overview, purchase link or details, journal prompts, imagery.
5. Healing Rooms / Ministry – explain ministry offerings, invite participation, testimonials or case-studies.
6. Live Stream & Links Page – page listing links for YouTube live stream, other platforms, archive links; simple layout.

Colour & Branding

Use colours that blend with our existing logo (attached). The palette should feel contemporary, welcoming, and aligned with ministry themes of restoration, healing and love. Ensure text, button and link colours maintain good contrast for accessibility.

Existing Content & Reference

Please gather available content from our current website in the attachment here for text, images and structure for reuse.

Imagery Guidelines

– Use original photos from our Facebook page or Google Location listing for building or people images when available.
– If generic images are used, ensure they depict appropriate ministry-related buildings or people (community, warm gathering) — avoid generic unrelated stock imagery.
– All photos must be royalty-free or have proper licensing and attribution.
– No overlapping objects or visual clutter; clean layouts with defined sections.

Additional Notes

– Integration: We currently utilise MailChimp for email communication; the design should include a connection/invite to subscribe (via MailChimp) but no blog page is required at this time.
– Payment/Giving: We accept PayPal and already have a giving portal; include clear donation/give buttons or calls-to-action linking to existing giving systems.
– No search function to be included.
– Layouts should avoid complex layering or overlapping elements—designers should work with distinct content blocks, clear visual hierarchy, and straightforward mobile-friendly structure.

Target Market(s)

Industry/Entity Type

Church/Religious institution

Number of Pages Required

5+ page

Requirements
Should not have
• search bar

```html
<!DOCTYPE html>
<html lang="en">
<head>
<meta charset="utf-8">
<title>Mended, Cherished, Whole</title>
<link rel="stylesheet" href="https://fonts.googleapis.com/css2?family=Fredoka:wght@500;600;700&family=Poppins:wght@400;500;600&display=swap">
<style>
:root{
  --teal:#00a89c;
  --green:#0d6b3a;
  --green-foot:#0b7a43;
  --purple:#6a2c91;
  --ink:#1d1d1d;
  --grey:#555;
  --soft:#f6f6f6;
  --white:#fff;
}
*{box-sizing:border-box;margin:0;padding:0}
html,body{width:1200px;height:3186px;overflow:hidden}
body{position:relative;font-family:"Poppins",sans-serif;color:var(--ink);background:var(--white)}
.abs{position:absolute}
.heading{font-family:"Fredoka",sans-serif;font-weight:700}
.btn{position:absolute;display:flex;align-items:center;justify-content:center;background:var(--purple);color:var(--white);font-family:"Poppins",sans-serif;font-weight:600;font-size:15px;border-radius:30px;white-space:nowrap}

/* header */
.site-header{position:absolute;left:0;top:0;width:1200px;height:86px;background:var(--white)}
.brand{position:absolute;left:145px;top:14px;display:flex;align-items:center;gap:10px}
.brand-dot{width:48px;height:48px;border-radius:50%;background:var(--teal)}
.brand-name{font-family:"Poppins",sans-serif;font-weight:600;font-size:20px;line-height:21px;color:var(--green)}
.utility{position:absolute;top:16px;right:145px;display:flex;align-items:center;gap:18px;font-size:13px;color:#333}
.utility span{display:flex;align-items:center;gap:6px}
.utility .sep{width:1px;height:18px;background:#ccc}
.utility .give{color:var(--purple);font-weight:600}
.main-nav{position:absolute;top:52px;right:145px;display:flex;gap:27px;font-size:15px;font-weight:500;color:#222}
.main-nav .active{color:var(--purple)}

/* hero */
.hero{position:absolute;left:0;top:86px;width:1200px;height:600px;overflow:hidden;
  background:linear-gradient(100deg,#4d4a22 0%,#6f7634 30%,#8c8a5e 55%,#b38a6a 70%,#7a8f4b 100%)}
.hero-title{position:absolute;left:145px;top:80px;font-size:44px;line-height:60px;color:var(--white)}
.hero-text{position:absolute;left:145px;top:212px;width:440px;font-size:16px;line-height:26px;color:var(--white)}
.hero .btn{left:145px;top:356px;width:158px;height:48px;border:2px solid var(--white);font-size:16px}

/* mission */
.mission-art{position:absolute;left:150px;top:705px;width:395px;height:360px;border-radius:48% 52% 44% 56%;
  background:linear-gradient(135deg,#0e9a88 0%,#1a8f7d 45%,#0a6f62 100%)}
.mission-title{position:absolute;left:620px;top:750px;font-size:36px;color:var(--green);font-weight:600}
.mission-text{position:absolute;left:622px;top:812px;width:434px;font-size:14px;line-height:24px;color:var(--grey);text-align:justify}
.mission .btn{left:622px;top:964px;width:136px;height:44px}

/* gathering */
.gathering{position:absolute;left:0;top:1120px;width:1200px;height:446px;background:var(--soft);text-align:center}
.gathering-title{position:absolute;left:0;width:1200px;top:45px;font-size:37px;color:var(--green);font-weight:600}
.gathering-lead{position:absolute;left:135px;width:930px;top:105px;font-size:16px;line-height:29px;color:#111}
.gathering-body{position:absolute;left:145px;width:910px;top:173px;font-size:13.5px;line-height:23.5px;color:var(--grey)}
.gathering-body p+p{margin-top:6px}
.gathering .btn{left:532px;top:347px;width:136px;height:44px}

/* who */
.who{position:absolute;left:0;top:1566px;width:1200px;height:518px;background:var(--teal);overflow:hidden}
.who-photo{position:absolute;left:600px;top:-220px;width:960px;height:960px;border-radius:50%;
  background:linear-gradient(120deg,#d9d4c8 0%,#8c8fa8 35%,#4d4f78 60%,#2f2b59 100%)}
.who-title{position:absolute;left:142px;top:45px;font-size:34px;color:var(--white);font-weight:600}
.who-lead{position:absolute;left:143px;top:104px;width:420px;font-size:16px;line-height:24px;font-weight:500;color:var(--white)}
.who-text{position:absolute;left:143px;top:182px;width:410px;font-size:13px;line-height:23.5px;color:var(--white)}
.who-text p+p{margin-top:6px}
.who .btn{left:143px;top:384px;width:136px;height:44px}

/* meaning */
.meaning-title{position:absolute;left:0;width:1200px;top:2155px;text-align:center;font-size:52px;line-height:64px;color:var(--ink)}
.t-teal{color:var(--teal)} .t-purple{color:var(--purple)} .t-green{color:var(--green)}
.meaning .btn{left:460px;top:2319px;width:280px;height:44px}
.meaning-scene{position:absolute;left:0;top:2370px;width:1200px;height:520px;
  background:linear-gradient(90deg,#1d2c45 0%,#2a3d5c 25%,#3e5a4f 48%,#8aa24a 55%,#bcd36a 75%,#7fbf4d 100%)}
.meaning-scene::after{content:"";position:absolute;inset:0;background:linear-gradient(180deg,#fff 0%,rgba(255,255,255,0) 25%)}

/* footer */
.site-footer{position:absolute;left:0;top:2860px;width:1200px;height:326px;background:var(--green-foot);color:var(--white)}
.foot-brand{position:absolute;left:145px;top:45px;display:flex;align-items:center;gap:10px}
.foot-brand .brand-dot{background:var(--white)}
.foot-brand .brand-name{color:var(--white);font-size:22px;line-height:24px}
.social{position:absolute;left:163px;top:152px;display:flex;gap:10px}
.social span{width:28px;height:28px;border-radius:50%;background:var(--white)}
.social span.on{background:var(--purple)}
.foot-head{position:absolute;top:46px;font-size:15px;font-weight:600;letter-spacing:.3px}
.foot-links{position:absolute;left:511px;top:80px;list-style:none;font-size:14px;line-height:24px}
.newsletter{position:absolute;left:814px;top:70px;width:242px}
.field{height:40px;background:var(--white);border-radius:4px;border:1px solid #ddd;margin-bottom:8px;font-size:9px;color:#777;padding:14px 10px}
.newsletter .btn{position:relative;margin-top:15px;width:136px;height:40px;font-size:14px}
.foot-rule{position:absolute;left:145px;top:290px;width:910px;height:1px;background:rgba(255,255,255,.3)}
.copyright{position:absolute;left:0;width:1200px;top:300px;text-align:center;font-size:13px}
</style>
</head>
<body>

<header class="site-header">
  <div class="brand"><span class="brand-dot"></span><span class="brand-name">Mended<br>Cherished<br>Whole</span></div>
  <div class="utility">
    <span class="give"><svg width="13" height="12" viewBox="0 0 13 12"><path d="M6.5 11.5 1.2 6.3A3 3 0 0 1 6.5 2a3 3 0 0 1 5.3 4.3Z" fill="#6a2c91"/></svg>Give Now</span>
    <span class="sep"></span>
    <span><svg width="13" height="12" viewBox="0 0 13 12"><path d="M0 1h2.5l1.6 6.5h7l1.4-5H3.4" fill="#00a89c"/><circle cx="5" cy="10.3" r="1.2" fill="#00a89c"/><circle cx="10" cy="10.3" r="1.2" fill="#00a89c"/></svg>My Cart</span>
  </div>
  <nav class="main-nav">
    <span class="active">Home</span><span>About Us</span><span>Meetings &amp; Events</span><span>Encounter</span><span>Healing Rooms</span><span>Live Stream</span>
  </nav>
</header>

<section class="hero" role="img" aria-label="Smiling older couple embracing in a sunlit meadow">
  <h1 class="hero-title heading">From Mended To<br>Mended, Cherished, Whole</h1>
  <p class="hero-text">Their desire is to share the love of Christ with others. They have numerous stories to share about the many ways they have seen God move in their lives as well as the lives of others.</p>
  <span class="btn">Get Started</span>
</section>
<svg class="abs" style="left:0;top:570px" width="1200" height="130" viewBox="0 0 1200 130">
  <path d="M0 106 C150 40 330 10 480 35 C600 55 640 100 700 105 C830 116 1000 70 1200 -2 L1200 130 L0 130Z" fill="#00a89c"/>
  <path d="M0 120 C150 62 330 36 470 56 C580 74 620 116 700 122 C830 130 1010 84 1200 12 L1200 130 L0 130Z" fill="#fff"/>
</svg>

<section class="mission">
  <div class="mission-art" role="img" aria-label="Large decorative teal ribbon artwork"></div>
  <h2 class="mission-title heading">Our Mission &amp; Vision</h2>
  <p class="mission-text">Honoring God’s presence by loving the broken, saving the lost, and healing the hurting through the demonstration of His love and power. Mended, Cherished, Whole is here to activate, proclaim &amp; teach the love of the Father through Jesus with the guidance of the Holy Spirit.</p>
  <span class="btn">Read More</span>
</section>

<section class="gathering">
  <h2 class="gathering-title heading">Gathering Invitation</h2>
  <p class="gathering-lead">If you are hosting an event at your church or ministry, as you prayerfully seek the Lord for guidance review these thoughts regarding Clara Jean &amp; Samuel Hollander and their ministry.</p>
  <div class="gathering-body">
    <p>I have served in church leadership with Clara Jean and Samuel for several years, and I do not know of a more balanced &amp; powerful ministry of miracles and healings. They are activators not only of supernatural demonstrations but of supernatural compassion. Every time I have been involved in their ministry, I have received something rich and liberating. I also have witnessed the body of Christ massively blest and equipped to carry the supernatural power of the gospel.</p>
    <p>They are people of integrity and love. Clara Jean and Samuel have the capacity to mightily impact local fellowships with authentic gospel power for the cause of Jesus Christ. This couple is truly a miracle-working gift to the Body of Christ. by MLW</p>
  </div>
  <span class="btn">Learn More</span>
</section>

<section class="who">
  <div class="who-photo" role="img" aria-label="Portrait of the ministry couple standing before a stained glass window"></div>
  <h2 class="who-title heading">Who Are We?</h2>
  <p class="who-lead">Samuel and Clara Jean have been married for 42 years and have two adult children. They both grew up in southern Illinois.</p>
  <div class="who-text">
    <p>Their desire is to share the love of Christ with others. They have numerous stories to share about the many ways they have seen God move in their lives as well as the lives of others. They believe in the manifestation of God’s power through signs and wonders.</p>
    <p>They have not only witnessed God’s power through signs and wonders them they have also experienced His miraculous healing touch personally.</p>
  </div>
  <span class="btn">Read More</span>
</section>

<section class="meaning">
  <h2 class="meaning-title heading"><span class="t-teal">What</span> Does It Mean To Be <span class="t-purple">Mended,</span><br><span class="t-green">Cherished</span>, and Whole?</h2>
  <div class="meaning-scene" role="img" aria-label="Tree split between a moonlit night and a sunny meadow with butterflies"></div>
  <span class="btn">Take A Moment To Learn More</span>
</section>
<svg class="abs" style="left:0;top:2750px" width="1200" height="120" viewBox="0 0 1200 120">
  <path d="M0 112 C150 40 330 -5 520 25 C640 45 700 95 800 95 C950 95 1080 40 1200 10 L1200 120 L0 120Z" fill="#00a89c"/>
  <path d="M0 120 C150 60 330 15 520 40 C640 60 690 108 800 110 C950 112 1080 55 1200 24 L1200 120Z" fill="#0b7a43"/>
</svg>

<footer class="site-footer">
  <div class="foot-brand"><span class="brand-dot"></span><span class="brand-name">Mended<br>Cherished<br>Whole</span></div>
  <div class="social"><span></span><span class="on"></span><span></span><span></span></div>
  <h3 class="foot-head" style="left:510px">LINKS</h3>
  <ul class="foot-links"><li>Home</li><li>About Us</li><li>Meetings &amp; Events</li><li>Encounter</li><li>Healing Rooms</li><li>Live Stream</li></ul>
  <h3 class="foot-head" style="left:814px">JOIN OUR NEWSLETTER</h3>
  <form class="newsletter">
    <div class="field">Full Name *</div>
    <div class="field">Last Name*</div>
    <div class="field">Email Address*</div>
    <span class="btn">Subcribe Now</span>
  </form>
  <div class="foot-rule"></div>
  <p class="copyright">© 2025 Mended, Cherished, Whole | All Rights Reserved</p>
</footer>

</body>
</html>
```